Law Firm Logo and Business Card Design

I need a logo and business card design for a law firm I just started. The law firm is named Law Office of Doreen K. Ashworth, LLC. The type of law I practice is Family Law, which includes divorce, custody, child support, alimony, property division, and the like. I would like to see designs that are unique and modern, yet sophisticated. I would also like to use the logo/design for my letterhead. I am not opposed to using some form of the scales of justice although I'd like something other than the typical, old fashioned scales of justice. I had considered a house made out of puzzle pieces with one puzzle piece pulled away from the others, with the logo text reading "Putting your life back together, one piece at a time." However, I don't want that particular design to look juvenile. I also would not be opposed to some form of my initials on the logo -- my initials are DKA. I am open to any other ideas you may have. I would like to see raised designs/lettering, and/or metallic finish. I like the colors black, white, gold, silver, and/or teal.

Industry/Entity Type

Law Firm

```html
<!DOCTYPE html>
<html lang="en">
<head>
<meta charset="utf-8">
<title>Law Office of Doreen K. Ashworth, LLC — Business Card</title>
<link rel="stylesheet" href="https://fonts.googleapis.com/css2?family=Tinos&display=swap">
<style>
  :root {
    --backdrop: #000000;
    --card-white: #ffffff;
    --brand-red: #990000;
    --logo-red: #9b0a0a;
    --rule-grey: #6e6e6e;
    --text-light: #ffffff;
  }
  * { margin: 0; padding: 0; box-sizing: border-box; }
  html, body {
    width: 1200px;
    height: 1200px;
    overflow: hidden;
    background: var(--backdrop);
  }
  .canvas {
    position: relative;
    width: 1200px;
    height: 1200px;
    background: var(--backdrop);
  }
  .business-card {
    position: absolute;
    left: 199px;
    top: 326px;
    width: 802px;
    height: 544px;
    background: var(--card-white);
    font-family: "Tinos", "Times New Roman", serif;
    overflow: hidden;
  }
  .brand-header {
    height: 212px;
    padding-top: 36px;
    display: flex;
    flex-direction: column;
    align-items: center;
    color: var(--logo-red);
    font-weight: 400;
    text-align: center;
  }
  .brand-mark {
    width: 56px;
    height: 56px;
    background: var(--logo-red);
  }
  .brand-subtitle-row {
    margin-top: 26px;
    display: flex;
    align-items: center;
    gap: 14px;
    height: 26px;
  }
  .divider-rule {
    width: 140px;
    height: 2px;
  }
  .divider-rule.left  { background: linear-gradient(to right, rgba(110,110,110,0), var(--rule-grey)); }
  .divider-rule.right { background: linear-gradient(to left, rgba(110,110,110,0), var(--rule-grey)); }
  .brand-subtitle {
    font-size: 22px;
    line-height: 26px;
    letter-spacing: 3px;
    text-transform: uppercase;
  }
  .brand-name {
    margin-top: 3px;
    font-size: 34px;
    line-height: 36px;
    letter-spacing: 1px;
    text-transform: uppercase;
  }
  .contact-panel {
    height: 332px;
    background: var(--brand-red);
    color: var(--text-light);
    text-align: center;
    font-size: 29px;
    line-height: 36px;
    padding-top: 30px;
  }
  .contact-group { font-style: normal; }
  .contact-group + .contact-group { margin-top: 32px; }
</style>
</head>
<body>
  <main class="canvas">
    <section class="business-card">
      <header class="brand-header">
        <div class="brand-mark"></div>
        <div class="brand-subtitle-row">
          <span class="divider-rule left"></span>
          <span class="brand-subtitle">Law Office of</span>
          <span class="divider-rule right"></span>
        </div>
        <div class="brand-name">Doreen K. Ashworth, LLC.</div>
      </header>
      <div class="contact-panel">
        <address class="contact-group">
          <div>2418 Harbor Point Blvd.</div>
          <div>Suite 310</div>
          <div>Riverton, MD 21409</div>
        </address>
        <div class="contact-group">
          <div>Phone : 443-555-0172</div>
        </div>
        <div class="contact-group">
          <div>www.ashworthfamilylaw.com</div>
          <div>doreen@ashworthfamilylaw.com</div>
        </div>
      </div>
    </section>
  </main>
</body>
</html>
```